VORTEQ

It’s is a startup business. We design and build new products.

Target Market(s)

For my first two products, they are targeting the laundry market, hanger accessory, and new modern style clothes dryer. I also have a Pet Treat product at patent stage, and there are other products not yet started but will be more engineering based. Therefore from young adults to older population

Industry/Entity Type

Colours of website to match the logo (att)

Coding

Coded - Design and coding required

Number of Pages Required

1 page

Font styles to use
Other font styles liked:
• Some of the same font as the logo

Colors

Designer to choose colors to be used in the design.

Requirements
Must have
• An upbeat vibe - the logo looks great so inline with that !
Should not have
• anything old fashioned and old style fonts

```html
<!DOCTYPE html>
<html lang="en">
<head>
<meta charset="utf-8">
<title>VORTEQ – Innovating Everyday Life</title>
<link href="https://fonts.googleapis.com/css2?family=Exo+2:wght@500;600;700&family=Mulish:wght@400;600;700;800&display=swap" rel="stylesheet">
<style>
:root{
  --teal:#1fd3c3;
  --teal-dark:#12b5a7;
  --navy:#1b2464;
  --navy-deep:#0f1748;
  --ink:#1e1e24;
  --muted:#55586a;
  --ice:#e5fbfb;
  --white:#ffffff;
  --footer:#353538;
  --line:#d9dde6;
}
*{margin:0;padding:0;box-sizing:border-box}
html,body{width:1200px;height:3112px;overflow:hidden;background:var(--white)}
body{font-family:"Mulish",sans-serif;color:var(--ink)}
h1,h2,h3,h4,.brand{font-family:"Exo 2",sans-serif}
.wrap{width:896px;margin:0 auto;position:relative;height:100%}
.btn{display:inline-block;background:var(--teal);color:var(--white);font-weight:800;font-size:11px;letter-spacing:.5px;padding:9px 20px;border-radius:20px;text-decoration:none}

/* header */
.site-header{height:120px;background:var(--white)}
.brand{position:absolute;left:0;top:26px;display:flex;align-items:center;gap:12px;font-size:40px;font-weight:700;color:var(--navy);letter-spacing:2px}
.brand-dot{width:22px;height:22px;border-radius:50%;background:var(--teal)}
.follow{position:absolute;left:460px;top:20px;display:flex;align-items:center;gap:8px;font-size:11px;font-weight:700;color:var(--navy)}
.social{width:22px;height:22px;border-radius:50%;background:var(--navy)}
.call{position:absolute;left:716px;top:14px;display:flex;align-items:center;gap:10px}
.call small{display:block;font-size:10px;font-weight:700;color:var(--navy)}
.call strong{font-size:17px;color:var(--navy);font-weight:700;white-space:nowrap}
.nav{position:absolute;right:0;top:74px;display:flex;gap:24px;list-style:none;font-size:12px;font-weight:700;color:var(--ink)}
.nav li.active{border-bottom:2px solid var(--teal);padding-bottom:4px}

/* hero */
.hero{height:560px;position:relative;background:radial-gradient(ellipse at 50% 80%,#2c5fd0 0%,#163a96 35%,#0b1a55 70%,#06103a 100%);text-align:center;color:var(--white)}
.hero h1{padding-top:58px;font-size:40px;font-weight:700;letter-spacing:2px}
.hero p{font-size:21px;line-height:1.4;margin:14px auto 0;width:560px}
.hero .btn{margin-top:26px;font-size:13px;padding:12px 26px}
.dots{position:absolute;left:0;right:0;bottom:44px;display:flex;justify-content:center;gap:12px}
.dots span{width:10px;height:10px;border-radius:50%;background:#fff;opacity:.6}
.dots span.on{opacity:1}

/* about */
.about{height:500px}
.about-photo{position:absolute;left:0;top:48px;width:448px;height:412px;border-radius:14px;background:linear-gradient(135deg,#cfd8e6,#7d8aa3 55%,#3a4358)}
.about-text{position:absolute;left:492px;top:100px;width:380px}
.about-text h2{font-size:28px;line-height:1.25;font-weight:700;color:var(--ink)}
.about-text .bar{width:60px;height:3px;background:var(--teal);margin:14px 0 18px}
.about-text p{font-size:15px;line-height:1.6;color:var(--muted);margin-bottom:28px}

/* products */
.products{height:532px;background:var(--ice)}
.section-title{text-align:center;font-size:30px;font-weight:700;padding-top:46px;color:var(--ink)}
.section-title::after{content:"";display:block;width:60px;height:3px;background:var(--teal);margin:12px auto 0}
.cards{position:absolute;top:152px;left:0;display:flex;gap:24px}
.product{width:436px;height:336px;background:var(--white);border-radius:12px;box-shadow:0 4px 14px rgba(0,0,0,.08);display:flex;align-items:center;padding:28px 22px;gap:20px}
.product-photo{flex:0 0 180px;width:180px;height:270px;border-radius:8px;background:linear-gradient(160deg,#f4eee8,#d6b79a)}
.product-photo.rack{background:linear-gradient(160deg,#f3f0ed,#b59b8a)}
.product-info{flex:1;min-width:0}
.product h3{font-size:24px;font-weight:600;margin:0 0 12px}
.product p{font-size:11.5px;line-height:1.55;color:var(--muted);margin-bottom:16px}

/* innovation */
.innovation{height:468px;background:linear-gradient(90deg,var(--navy) 0%,var(--navy-deep) 100%);color:var(--white)}
.innovation-text{position:absolute;left:0;top:52px;width:400px}
.innovation-text h2{font-size:28px;font-weight:700;letter-spacing:.5px}
.innovation-text .bar{width:60px;height:3px;background:var(--teal);margin:14px 0 22px}
.innovation-text p{font-size:15px;line-height:1.6;opacity:.9}
.innovation-text ul{margin:16px 0 26px 20px;font-size:15px;line-height:1.9}
.innovation-photo{position:absolute;left:456px;top:0;width:440px;height:468px;background:radial-gradient(circle at 50% 45%,#9be8ff 0%,#2c7fd8 30%,#123a8a 65%,#0a1850 100%)}

/* blog */
.blog{height:708px}
.posts{position:absolute;top:132px;left:0;display:flex;gap:16px}
.post{width:288px;height:536px;border-radius:12px;box-shadow:0 4px 14px rgba(0,0,0,.1);overflow:hidden;background:var(--white)}
.post-photo{height:240px;background:linear-gradient(135deg,#a6b6cc,#4d5e7a)}
.post-photo.two{background:linear-gradient(135deg,#d8d2c9,#8c7f70)}
.post-photo.three{background:linear-gradient(135deg,#b9cde0,#3f5d82)}
.post-body{padding:22px 20px}
.post h4{font-size:15px;font-weight:700;line-height:1.35;margin-bottom:12px}
.post p{font-size:12px;line-height:1.55;color:var(--muted);margin-bottom:18px}

/* footer */
.site-footer{height:224px;background:var(--footer);color:var(--white)}
.site-footer .brand{color:var(--white);top:52px}
.f-col{position:absolute;top:30px;font-size:11px;line-height:1.9}
.f-col h4{font-size:15px;font-weight:700;margin-bottom:8px}
.f-col.contact{left:420px}
.f-col.menu{left:656px}
.f-col.follow-col{left:764px}
.f-item{display:flex;gap:8px;align-items:flex-start;margin-bottom:6px}
.f-ico{width:18px;height:18px;border-radius:50%;background:var(--teal);flex:none}
.f-social{display:flex;gap:8px}
.f-social span{width:24px;height:24px;border-radius:50%;background:var(--white)}
.copyright{position:absolute;left:0;right:0;top:186px;text-align:center;font-size:10px;opacity:.8}
</style>
</head>
<body>

<header class="site-header">
  <div class="wrap">
    <div class="brand"><span class="brand-dot"></span>VORTEQ</div>
    <div class="follow">FOLLOW US <span class="social"></span><span class="social"></span><span class="social"></span><span class="social"></span><span class="social"></span></div>
    <div class="call">
      <svg width="28" height="28" viewBox="0 0 24 24"><path d="M6.6 10.8a15 15 0 0 0 6.6 6.6l2.2-2.2a1 1 0 0 1 1-.25 11.4 11.4 0 0 0 3.6.57 1 1 0 0 1 1 1V20a1 1 0 0 1-1 1A17 17 0 0 1 3 4a1 1 0 0 1 1-1h3.5a1 1 0 0 1 1 1c0 1.25.2 2.45.57 3.57a1 1 0 0 1-.25 1z" fill="#1b2464"/></svg>
      <div><small>CALL US</small><strong>+1 555 010 2040</strong></div>
    </div>
    <ul class="nav">
      <li class="active">HOME</li><li>ABOUT US</li><li>SERVICES</li><li>PRODUCTS</li><li>BLOG</li><li>CONTACT US</li>
    </ul>
  </div>
</header>

<section class="hero" role="img" aria-label="Glowing blue digital particle wave background">
  <h1>INNOVATING EVERYDAY LIFE</h1>
  <p>Smart designs, modern solutions - engineering the future, one product at a time.</p>
  <a class="btn">READ MORE</a>
  <div class="dots"><span class="on"></span><span></span><span></span><span></span></div>
</section>

<section class="about">
  <div class="wrap">
    <div class="about-photo" role="img" aria-label="Designer working at a computer with product sketches on screen"></div>
    <div class="about-text">
      <h2>DRIVEN BY INNOVATION, ENGINEERED FOR LIFE</h2>
      <div class="bar"></div>
      <p>Vorteq is a startup committed to developing innovative solutions for modern living. Our team of designers and engineers creates groundbreaking products that redefine convenience and functionality. With a passion for smart design, we bridge the gap between technology and everyday needs.</p>
      <a class="btn">READ MORE</a>
    </div>
  </div>
</section>

<section class="products">
  <div class="wrap">
    <h2 class="section-title">OUR PRODUCTS</h2>
    <div class="cards">
      <article class="product">
        <div class="product-photo" role="img" aria-label="Wooden and black clothes hangers"></div>
        <div class="product-info">
          <h3>PRODUCT 1</h3>
          <p>Lorem ipsum dolor sit amet, consectetur adipiscing elit, sed do eiusmod tempor incididunt ut labore et dolore magna aliqua. Ut enim ad minim veniam, quis nostrud exercitation ullamco laboris nisi ut aliquip ex ea commodo consequat.</p>
          <a class="btn">READ MORE</a>
        </div>
      </article>
      <article class="product">
        <div class="product-photo rack" role="img" aria-label="Folding clothes drying rack"></div>
        <div class="product-info">
          <h3>PRODUCT 2</h3>
          <p>Lorem ipsum dolor sit amet, consectetur adipiscing elit, sed do eiusmod tempor incididunt ut labore et dolore magna aliqua. Ut enim ad minim veniam, quis nostrud exercitation ullamco laboris nisi ut aliquip ex ea commodo consequat.</p>
          <a class="btn">READ MORE</a>
        </div>
      </article>
    </div>
  </div>
</section>

<section class="innovation">
  <div class="wrap">
    <div class="innovation-text">
      <h2>INNOVATION &amp; ENGINEERING</h2>
      <div class="bar"></div>
      <p>Every product at Vorteq is born from a deep understanding of design, engineering, and user experience. Our approach includes:</p>
      <ul>
        <li>Research-driven development</li>
        <li>Modern aesthetics with practical use</li>
        <li>Patent-backed innovations</li>
      </ul>
      <a class="btn">READ MORE</a>
    </div>
    <div class="innovation-photo" role="img" aria-label="Hand touching a glowing lightbulb surrounded by technology icons"></div>
  </div>
</section>

<section class="blog">
  <div class="wrap">
    <h2 class="section-title">LATEST BLOG</h2>
    <div class="posts">
      <article class="post">
        <div class="post-photo" role="img" aria-label="Team collaborating around laptops"></div>
        <div class="post-body">
          <h4>LOREM IPSUM DOLOR SIT AMET, CONSECTETUR ADIPIS CING ELIT</h4>
          <p>Lorem ipsum dolor sit amet, consectetur adipiscing elit, sed do eiusmod tempor incididunt ut labore et dolore magna aliqua.</p>
          <a class="btn">READ MORE</a>
        </div>
      </article>
      <article class="post">
        <div class="post-photo two" role="img" aria-label="Designers reviewing product sketches at a table"></div>
        <div class="post-body">
          <h4>LOREM IPSUM DOLOR SIT AMET, CONSECTETUR ADIPIS CING ELIT</h4>
          <p>Lorem ipsum dolor sit amet, consectetur adipiscing elit, sed do eiusmod tempor incididunt ut labore et dolore magna aliqua.</p>
          <a class="btn">READ MORE</a>
        </div>
      </article>
      <article class="post">
        <div class="post-photo three" role="img" aria-label="Engineer working with technical screens"></div>
        <div class="post-body">
          <h4>LOREM IPSUM DOLOR SIT AMET, CONSECTETUR ADIPIS CING ELIT</h4>
          <p>Lorem ipsum dolor sit amet, consectetur adipiscing elit, sed do eiusmod tempor incididunt ut labore et dolore magna aliqua.</p>
          <a class="btn">READ MORE</a>
        </div>
      </article>
    </div>
  </div>
</section>

<footer class="site-footer">
  <div class="wrap">
    <div class="brand"><span class="brand-dot"></span>VORTEQ</div>
    <div class="f-col contact">
      <h4>CONTACT US</h4>
      <div class="f-item"><span class="f-ico"></span><span>410 Harbor Lane, Suite B,<br>Brookfield, TN 37000</span></div>
      <div class="f-item"><span class="f-ico"></span><span>+1 555 010 2040</span></div>
      <div class="f-item"><span class="f-ico"></span><span>info@vorteq.com</span></div>
    </div>
    <div class="f-col menu">
      <h4>MENU</h4>
      Home<br>About Us<br>Services<br>Products<br>Blog<br>Contact Us
    </div>
    <div class="f-col follow-col">
      <h4>FOLLOW US</h4>
      <div class="f-social"><span></span><span></span><span></span><span></span><span></span></div>
    </div>
    <div class="copyright">Copyright © 2025 All Rights Reserved</div>
  </div>
</footer>

</body>
</html>
```